Lumavento business card

We need a modern business card - With our 4 colors - See web: www.lumavento.dk

I have attached logo and som old business Cards we have - Lets Make the new ones shine...:-) -

Industry/Entity Type

Business

Requirements
Must have
• the logo with lumavento only,

```html
<!DOCTYPE html>
<html lang="da">
<head>
<meta charset="utf-8">
<title>Lumavento visitkort</title>
<link rel="stylesheet" href="https://fonts.googleapis.com/css2?family=Open+Sans:wght@400;600&display=swap">
<style>
  :root {
    --page: #e4e4e4;
    --card-dark: #1f1b1c;
    --card-light: #ffffff;
    --lime: #8cc63f;
    --ink: #4a4a4a;
    --ink-soft: #6d6d6d;
    --rule: #c9c9c9;
    --on-dark: #ffffff;
  }
  * { margin: 0; padding: 0; box-sizing: border-box; }
  html, body { width: 1200px; height: 950px; overflow: hidden; }
  body {
    background: var(--page);
    font-family: "Open Sans", Arial, sans-serif;
    position: relative;
  }
  .card {
    position: absolute;
    left: 250px;
    width: 700px;
    height: 400px;
    box-shadow: 0 6px 18px rgba(0,0,0,.18);
  }
  .card--back { top: 50px; background: var(--card-dark); }
  .card--front { top: 500px; background: var(--card-light); color: var(--ink); }

  .back-brand {
    position: absolute;
    right: 70px;
    bottom: 150px;
    font-size: 30px;
    font-weight: 400;
    letter-spacing: 2px;
    color: var(--on-dark);
  }

  .brand {
    position: absolute;
    left: 390px;
    top: 45px;
    width: 240px;
  }
  .brand-name {
    display: flex;
    align-items: center;
    gap: 10px;
    font-size: 30px;
    font-weight: 400;
    letter-spacing: 2px;
    color: var(--lime);
  }
  .brand-dot {
    width: 16px; height: 16px; border-radius: 50%;
    background: var(--lime);
  }
  .brand-rule { height: 2px; background: var(--lime); margin-top: 8px; }
  .brand-tagline {
    text-align: right;
    font-size: 12px;
    color: var(--ink);
    margin-top: 6px;
  }
  .card-rule {
    position: absolute;
    left: 390px; top: 150px;
    width: 240px; height: 1px;
    background: var(--rule);
  }

  .person {
    position: absolute;
    left: 50px; top: 190px;
    width: 270px;
  }
  .person-name {
    font-size: 24px;
    font-weight: 600;
    line-height: 1.35;
    color: var(--lime);
  }
  .person-title { font-size: 16px; color: var(--ink); margin-top: 2px; }
  .person-rule { height: 1px; background: var(--rule); margin: 12px 0 12px; }
  .contact-line { font-size: 15px; color: var(--ink-soft); line-height: 1.6; }
  .contact-label { color: var(--lime); font-weight: 600; }

  .divider {
    position: absolute;
    left: 345px; top: 200px;
    width: 1px; height: 80px;
    background: var(--rule);
  }
  .online {
    position: absolute;
    left: 375px; top: 203px;
  }
  .address {
    position: absolute;
    left: 50px; bottom: 28px;
    font-size: 15px;
    line-height: 1.4;
    color: var(--ink-soft);
  }
</style>
</head>
<body>
  <section class="card card--back" aria-label="Bagside">
    <div class="back-brand">lumavento</div>
  </section>

  <section class="card card--front" aria-label="Forside">
    <div class="brand">
      <div class="brand-name"><span class="brand-dot"></span>lumavento</div>
      <div class="brand-rule"></div>
      <div class="brand-tagline">lys og retning</div>
    </div>
    <div class="card-rule"></div>

    <div class="person">
      <div class="person-name">Maren Holstvig</div>
      <div class="person-title">Salgsdirektør</div>
      <div class="person-rule"></div>
      <div class="contact-line"><span class="contact-label">P</span> : +45 31 42 60 18</div>
      <div class="contact-line"><span class="contact-label">P</span> : +45 52 70 14 83</div>
    </div>

    <div class="divider"></div>
    <div class="online">
      <div class="contact-line"><span class="contact-label">E</span> : mh@lumavento.dk</div>
      <div class="contact-line"><span class="contact-label">W</span> : www.lumavento.dk</div>
    </div>

    <div class="address">Kastanievej 14, 2000 Frederiksberg Tlf.+45 31 42 60 18</div>
  </section>
</body>
</html>
```